A website for a Maltese Law Firm

Our law firm needs a website to further its business. The site should have a simple yet effective design. We would need the following sections: About us, Practice Areas, About Malta, Contact. These should be further split as follows:

About us: Our firm, Our values, What others say, Offices

Practice Areas: Crimimal, Citizenship & Residence, Sovereign Patron Pathway, Criminal Defence, Civil Litigation, Arbitration and ADR, Commercial and Corporate, Media Law.

About Malta: just one section.

Contact: Just one section

We would also need a news feed at the front of the site to include latest news regarding our cases.

At the bottom we need a section for our Terms and a Privacy Statement.

Our logo is being attached.

Target Market(s)

All clients looking for legal assistance in Malta

Industry/Entity Type

Legal

Coding

Coded - Design and coding required

Number of Pages Required

1 page

Requirements
Must have
• It must be simple yet striking.

```html
<!DOCTYPE html>
<html lang="en">
<head>
<meta charset="utf-8">
<title>Delacroix &amp; Vella Advocates</title>
<link rel="stylesheet" href="https://fonts.googleapis.com/css2?family=Cinzel:wght@400;700&family=Lato:ital,wght@0,400;0,700;1,400&display=swap">
<style>
:root{
  --ink:#1b1b1b;
  --header:#0f0f0f;
  --topbar:#1d1d1d;
  --paper:#ffffff;
  --mist:#f4f4f4;
  --text:#5a5a5a;
  --muted:#8c8c8c;
  --link:#2f8fd6;
  --tile-blue:#3d8fc9;
  --dark-band:#1c1511;
  --footer:#1a1a1a;
  --footer-bottom:#2b2b2b;
  --line:#cfcfcf;
}
*{box-sizing:border-box;margin:0;padding:0}
html,body{width:1200px;height:3727px;overflow:hidden}
body{font-family:"Lato",Arial,sans-serif;color:var(--text);background:var(--paper);position:relative}
.serif{font-family:"Cinzel",Georgia,serif}

/* header */
.site-header{position:absolute;left:0;top:0;width:1200px;height:112px;background:var(--header)}
.topbar{height:28px;background:var(--topbar);display:flex;align-items:center;justify-content:space-between;padding:0 82px}
.social-squares{display:flex;gap:4px}
.social-squares span{width:20px;height:20px;background:#2e2e2e;border:1px solid #3a3a3a}
.top-phone{display:flex;align-items:center;gap:8px;color:#ddd;font-size:13px}
.brand{position:absolute;left:103px;top:48px;font-family:"Cinzel",Georgia,serif;color:#fff;font-size:31px;letter-spacing:1px;border-bottom:1px solid #888;padding-bottom:6px}
.main-nav{position:absolute;left:523px;top:58px;display:flex;gap:36px}
.main-nav a{font-family:"Cinzel",Georgia,serif;color:#e8e8e8;font-size:17px;text-decoration:none;padding-bottom:4px}
.main-nav a.active{color:#fff;border-bottom:2px solid #fff}

/* hero */
.hero{position:absolute;left:0;top:112px;width:1200px;height:571px;background:linear-gradient(180deg,#6e7f88 0%,#9aa7ad 35%,#4d4d52 100%)}
.hero-caption{position:absolute;left:0;top:430px;padding:18px 60px 14px 103px;background:rgba(0,0,0,.45);font-family:"Cinzel",Georgia,serif;color:#fff;font-size:37px;line-height:49px;letter-spacing:1px}
.hero-arrow{position:absolute;top:300px;width:34px;height:44px;background:#111;display:flex;align-items:center;justify-content:center}
.hero-arrow.prev{left:10px}.hero-arrow.next{right:10px}

/* section headings */
.section-title{font-family:"Cinzel",Georgia,serif;font-size:38px;color:var(--ink);text-align:center;letter-spacing:1px}
.section-title .ruled{border-top:2px solid var(--ink);border-bottom:2px solid var(--ink);padding:0 2px}
.section-title.light{color:#fff}
.section-title.light .ruled{border-color:#fff}

/* about */
.about{position:absolute;left:0;top:683px;width:1200px;height:510px;background:var(--mist)}
.about .section-title{margin-top:44px}
.about-sub{text-align:center;font-family:"Cinzel",Georgia,serif;font-size:11px;letter-spacing:3px;color:#444;margin-top:2px}
.about-copy{width:1010px;margin:38px auto 0;text-align:center;font-size:14.5px;line-height:25px;color:#555}
.about-copy p+p{margin-top:24px}
.about-features{position:absolute;top:355px;left:208px;display:flex;gap:155px}
.feature{display:flex;gap:18px;width:380px}
.feature-icon{width:98px;height:98px;background:#fff;border:1px solid #ccc;display:flex;align-items:center;justify-content:center;flex:none}
.feature h3{font-family:"Cinzel",Georgia,serif;font-weight:400;font-size:18px;color:var(--ink);margin:4px 0 6px}
.feature p{font-size:13px;line-height:19px;color:#666}

/* practice areas */
.practice{position:absolute;left:0;top:1193px;width:1200px;height:1334px;background:var(--paper)}
.practice .section-title{margin-top:40px}
.practice-grid{position:absolute;left:80px;top:122px;display:grid;grid-template-columns:repeat(3,330px);grid-template-rows:repeat(3,355px);column-gap:25px;row-gap:25px}
.practice-tile{position:relative;overflow:hidden}
.practice-tile .photo{position:absolute;inset:0}
.practice-tile .label{position:absolute;left:0;right:0;bottom:30px;text-align:center;font-family:"Cinzel",Georgia,serif;color:#fff;font-size:25px;line-height:27px;letter-spacing:1px;text-shadow:0 1px 3px rgba(0,0,0,.4)}
.practice-tile.featured .label{bottom:auto;top:148px}
.tile-blurb{position:absolute;left:40px;right:40px;top:190px;text-align:center;color:#fff;font-size:14px;font-weight:700;line-height:21px}
.tile-plus{position:absolute;left:145px;top:278px}
.g-criminal{background:linear-gradient(180deg,#6f7b86 0%,#5c8fb8 55%,#3d8fcc 100%)}
.g-home{background:linear-gradient(180deg,#a9c2d8 0%,#8c8a7c 50%,#3f8fc8 100%)}
.g-meeting{background:linear-gradient(180deg,#d8d2c8 0%,#9aa7b0 55%,#3f8fc8 100%)}
.g-gavel{background:linear-gradient(180deg,#5a3a2a 0%,#6a6a70 55%,#3f8fc8 100%)}
.g-helmet{background:linear-gradient(180deg,#e0d7b8 0%,#c7b356 45%,#4c8fc0 100%)}
.g-media{background:linear-gradient(180deg,#cfcfcf 0%,#8b8e96 50%,#3f8fc8 100%)}
.g-office{background:linear-gradient(180deg,#4f5d66 0%,#6f8190 50%,#3d8fcc 100%)}
.g-tower{background:linear-gradient(180deg,#2e6aa8 0%,#7ca4c9 50%,#3b8bc8 100%)}
.g-cuffs{background:linear-gradient(180deg,#7f8589 0%,#6c8ea8 55%,#3d8fcc 100%)}

/* case studies */
.cases{position:absolute;left:0;top:2527px;width:1200px;height:525px;background:linear-gradient(180deg,#17110d 0%,#2a1f18 60%,#1a1410 100%)}
.cases .section-title{margin-top:36px}
.case-grid{position:absolute;left:80px;top:137px;display:flex;gap:55px}
.case-card{width:310px}
.case-thumb{position:relative;height:156px;border:5px solid #6d6d6d;background:linear-gradient(180deg,#5a4a34 0%,#3b3128 100%)}
.case-date{position:absolute;left:6px;top:6px;width:44px;text-align:center;background:#fff;font-size:12px;line-height:16px;color:#333}
.case-date b{display:block;background:#2a2a2a;color:#fff;font-size:14px;line-height:20px}
.case-card h4{margin-top:12px;font-size:13.5px;font-weight:700;color:var(--link)}
.case-card p{margin-top:8px;font-size:13px;line-height:19px;color:#ddd}
.case-card .more{display:block;margin-top:6px;font-size:13px;color:var(--link)}
.view-all{position:absolute;left:537px;top:452px;display:flex}
.view-all span{width:88px;height:30px;background:#d9d9d9;font-size:11px;color:#333;display:flex;align-items:center;justify-content:center}
.view-all i{width:34px;height:30px;background:#3a3a3a;display:flex;align-items:center;justify-content:center}

/* testimonials */
.testimonials{position:absolute;left:0;top:3052px;width:1200px;height:360px;background:var(--paper)}
.testimonials .section-title{margin-top:46px}
.quotes{position:absolute;left:95px;top:146px;display:flex}
.quote{display:flex;gap:22px;width:485px}
.quote+.quote{border-left:1px solid #ddd;margin-left:40px;padding-left:50px}
.avatar-wrap{width:100px;flex:none;text-align:center}
.avatar{width:96px;height:96px;border-radius:50%;border:4px solid #555;background:linear-gradient(180deg,#b9c3cc,#7c8894)}
.avatar-wrap .name{margin-top:12px;font-size:13px;font-weight:700;color:#222}
.quote p{font-style:italic;font-size:13.5px;line-height:22px;color:#777;width:360px}
.slide-arrow{position:absolute;top:192px;width:34px;height:34px;border-radius:50%;border:1px solid #bbb;display:flex;align-items:center;justify-content:center}

/* footer */
.site-footer{position:absolute;left:0;top:3412px;width:1200px;height:266px;background:var(--footer)}
.footer-col h5{font-family:"Lato",Arial,sans-serif;font-size:16px;font-weight:400;color:var(--link);letter-spacing:1px;text-transform:uppercase;border-bottom:1px solid #444;padding-bottom:10px;margin-bottom:14px}
.quick-links{position:absolute;left:82px;top:40px;width:140px}
.quick-links li{list-style:none;color:#ddd;font-size:12px;line-height:29px;display:flex;align-items:center;gap:8px}
.quick-links li::before{content:"";width:4px;height:4px;background:#ddd;border-radius:50%}
.contact{position:absolute;left:300px;top:40px;width:220px}
.contact .row{display:flex;gap:10px;color:#ddd;font-size:12px;line-height:17px;margin-bottom:12px}
.contact .row svg{flex:none;margin-top:2px}
.map{position:absolute;left:525px;top:96px;width:180px;height:112px;background:linear-gradient(135deg,#e6ecef,#c9d8e2);border:1px solid #999}
.footer-brand{position:absolute;left:860px;top:-6px;font-family:"Cinzel",Georgia,serif;font-size:23px;color:#fff;background:var(--paper);color:#222;padding:4px 14px}
.footer-circles{position:absolute;left:908px;top:47px;display:flex;gap:8px}
.footer-circles span{width:28px;height:28px;border-radius:50%}
.legal{position:absolute;left:898px;top:164px;font-size:11px;color:#555}
.legal span{margin:0 10px}
.copyright{position:absolute;left:0;top:3678px;width:1200px;height:49px;background:var(--footer-bottom);padding-left:94px;display:flex;align-items:center;font-size:12px;color:#bbb}
.copyright b{color:#eee;margin:0 4px}
</style>
</head>
<body>

<header class="site-header">
  <div class="topbar">
    <div class="social-squares"><span></span><span></span><span></span><span></span></div>
    <div class="top-phone">
      <svg width="12" height="16" viewBox="0 0 12 16"><rect x="1" y="0.5" width="10" height="15" rx="2" fill="#fff"/><rect x="3" y="2.5" width="6" height="9" fill="#1d1d1d"/></svg>
      555-014-2290
    </div>
  </div>
  <div class="brand">Delacroix &amp; Vella</div>
  <nav class="main-nav">
    <a class="active" href="#">Home</a>
    <a href="#">About Us</a>
    <a href="#">Practice Areas</a>
    <a href="#">Case Studies</a>
    <a href="#">Contact Us</a>
  </nav>
</header>

<section class="hero">
  <div class="hero-photo" role="img" aria-label="Photo of lawyers shaking hands across a meeting table" style="position:absolute;inset:0"></div>
  <div class="hero-caption">Realize Your Constitutional<br>Right For Qualified Legal Help</div>
  <div class="hero-arrow prev"><svg width="12" height="18" viewBox="0 0 12 18"><path d="M10 2 3 9l7 7" stroke="#fff" stroke-width="2.5" fill="none"/></svg></div>
  <div class="hero-arrow next"><svg width="12" height="18" viewBox="0 0 12 18"><path d="m2 2 7 7-7 7" stroke="#fff" stroke-width="2.5" fill="none"/></svg></div>
</section>

<section class="about">
  <h2 class="section-title">About <span class="ruled">Delacroix &amp; Vella</span></h2>
  <div class="about-sub">ADVOCATES</div>
  <div class="about-copy">
    <p>Lorem ipsum dolor sit amet, consectetuer adipiscing elit, sed diam nonummy nibh euismod tincidunt ut laoreet dolore magna aliquam erat volutpat. Ut wisi enim ad minim veniam, quis nostrud exerci tation ullamcorper suscipit lobortis nisl ut aliquip ex eam commodo consequat. Duis autem vel eum iriure dolor in hendrerit in vulputate velit molestie consequat nulla facilisi.</p>
    <p>Lorem ipsum dolor sit amet, consectetuer adipiscing elit, sed diam nonummy nibh euismod tincidunt ut laoreet dolore magna aliquam erat volutpat. Ut wisi enim ad minim veniam, quis nostrud exerci tation ullamcorper suscipit lobortis nisl ut aliquip ex eam commodo consequat. Duis autem vel eum iriure dolor in hendrerit in vulputate velit molestie consequat nulla facilisi.</p>
  </div>
  <div class="about-features">
    <div class="feature">
      <div class="feature-icon"><svg width="50" height="40" viewBox="0 0 50 40"><path d="M5 20 18 8l9 6 9-6 9 12-14 12-8-6-7 6z" fill="#333"/></svg></div>
      <div><h3>Our Values</h3><p>Artis nisl ut aliquip ex ea commodol eros et accumsan o dignss qui nulla facilisi..[+]</p></div>
    </div>
    <div class="feature">
      <div class="feature-icon"><svg width="48" height="44" viewBox="0 0 48 44"><path d="M24 2 2 13h44z" fill="#333"/><rect x="6" y="16" width="6" height="20" fill="#333"/><rect x="17" y="16" width="6" height="20" fill="#333"/><rect x="28" y="16" width="6" height="20" fill="#333"/><rect x="38" y="16" width="6" height="20" fill="#333"/><rect x="2" y="38" width="44" height="5" fill="#333"/></svg></div>
      <div><h3>Our firm</h3><p>Artis nisl ut aliquip ex ea commodol eros et accumsan o dignss qui nulla facilisi..[+]</p></div>
    </div>
  </div>
</section>

<section class="practice">
  <h2 class="section-title">Practice <span class="ruled">Areas</span></h2>
  <div class="practice-grid">
    <div class="practice-tile featured">
      <div class="photo g-criminal" role="img" aria-label="Photo of handcuffed hands"></div>
      <div class="label">Crimimal</div>
      <div class="tile-blurb">Lorem ipsum dolor sit amet, consectetuer adipiscing elit, sed diam nonummy nibh euismod</div>
      <svg class="tile-plus" width="40" height="40" viewBox="0 0 40 40"><circle cx="20" cy="20" r="18" stroke="#fff" stroke-width="2" fill="none"/><path d="M20 11v18M11 20h18" stroke="#fff" stroke-width="2"/></svg>
    </div>
    <div class="practice-tile"><div class="photo g-home" role="img" aria-label="Photo of a family in front of their house"></div><div class="label">Citizenship &amp;<br>Residence</div></div>
    <div class="practice-tile"><div class="photo g-meeting" role="img" aria-label="Photo of a couple meeting an advisor"></div><div class="label">Sovereign Patron<br>Pathway</div></div>
    <div class="practice-tile"><div class="photo g-gavel" role="img" aria-label="Photo of a judge's gavel"></div><div class="label">Criminal Defence</div></div>
    <div class="practice-tile"><div class="photo g-helmet" role="img" aria-label="Photo of a yellow hard hat held by a worker"></div><div class="label">Civil Litigation</div></div>
    <div class="practice-tile"><div class="photo g-media" role="img" aria-label="Photo of press microphones"></div><div class="label" style="bottom:auto;top:172px">Media Law</div></div>
    <div class="practice-tile"><div class="photo g-office" role="img" aria-label="Photo of two businessmen talking in an office"></div><div class="label">Arbitration<br>and ADR</div></div>
    <div class="practice-tile"><div class="photo g-tower" role="img" aria-label="Photo of a hand signing papers before office towers"></div><div class="label">Commercial and<br>Corporate</div></div>
    <div class="practice-tile"><div class="photo g-cuffs" role="img" aria-label="Photo of handcuffed hands"></div><div class="label" style="bottom:auto;top:185px">Crimimal</div></div>
  </div>
</section>

<section class="cases">
  <div role="img" aria-label="Dim background photo of law books and a gavel" style="position:absolute;inset:0"></div>
  <h2 class="section-title light" style="position:relative">Case <span class="ruled">Studies</span></h2>
  <div class="case-grid">
    <article class="case-card">
      <div class="case-thumb" role="img" aria-label="Photo of law books on a shelf"><div class="case-date"><b>06</b>Jun</div></div>
      <h4>Lorem Ipsum Dolor Sit Amet, Consectetur</h4>
      <p>Lorem ipsum dolor sit amet, consectetur adipiscing elit. Sed vitae magna tellus. Aenean ante nunc, semper nec cursus non, rutrum ac eros.</p>
      <span class="more">Read More »</span>
    </article>
    <article class="case-card">
      <div class="case-thumb" role="img" aria-label="Photo of handcuffed hands before a bench" style="background:linear-gradient(180deg,#6a5a4a,#2e2a28)"><div class="case-date"><b>06</b>Jun</div></div>
      <h4>Lorem Ipsum Dolor Sit Amet, Consectetur</h4>
      <p>Lorem ipsum dolor sit amet, consectetur adipiscing elit. Sed vitae magna tellus. Aenean ante nunc, semper nec cursus non, rutrum ac eros.</p>
      <span class="more">Read More »</span>
    </article>
    <article class="case-card">
      <div class="case-thumb" role="img" aria-label="Photo of a hand signing a document" style="background:linear-gradient(180deg,#8a8a88,#d8d6d0)"><div class="case-date"><b>07</b>Jun</div></div>
      <h4>Lorem Ipsum Dolor Sit Amet, Consectetur</h4>
      <p>Lorem ipsum dolor sit amet, consectetur adipiscing elit. Sed vitae magna tellus. Aenean ante nunc, semper nec cursus non, rutrum ac eros.</p>
      <span class="more">Read More »</span>
    </article>
  </div>
  <div class="view-all"><span>VIEW ALL</span><i><svg width="10" height="14" viewBox="0 0 10 14"><path d="m2 2 5 5-5 5" stroke="#fff" stroke-width="2" fill="none"/></svg></i></div>
</section>

<section class="testimonials">
  <h2 class="section-title">Client <span class="ruled">Testimonials</span></h2>
  <div class="slide-arrow" style="left:28px"><svg width="10" height="14" viewBox="0 0 10 14"><path d="M8 2 3 7l5 5" stroke="#999" stroke-width="2" fill="none"/></svg></div>
  <div class="quotes">
    <div class="quote">
      <div class="avatar-wrap"><div class="avatar" role="img" aria-label="Client portrait"></div><div class="name">- Mark Bonello</div></div>
      <p>“ Lorem ipsum sit amet co adipiscitsedutel eiusmo dtepor incidunt ut la dolore ma aliquaenil kni enim nim veni exercitation ullamco ips sdlitnel ameti co adipiscig elitsed do eiusmod te epo uon Accusant dol oremque laudantium. ”</p>
    </div>
    <div class="quote">
      <div class="avatar-wrap"><div class="avatar" role="img" aria-label="Client portrait"></div><div class="name">- Clara Azzopardi</div></div>
      <p>“ Lorem ipsum sit amet co adipiscitsedutel eiusmo dtepor incidunt ut la dolore ma aliquaenil kni enim nim veni exercitation ullamco ips sdlitnel ameti co adipiscig elitsed do eiusmod te epo uon Accusant dol oremque laudantium. ”</p>
    </div>
  </div>
  <div class="slide-arrow" style="right:28px;border-color:#555"><svg width="10" height="14" viewBox="0 0 10 14"><path d="m2 2 5 5-5 5" stroke="#333" stroke-width="2" fill="none"/></svg></div>
</section>

<footer class="site-footer">
  <div class="footer-col quick-links">
    <h5>Quick Links</h5>
    <ul><li>Home</li><li>About Malta</li><li>Practice Areas</li><li>Case Studies</li><li>Contact Us</li></ul>
  </div>
  <div class="footer-col contact">
    <h5>Contact Details</h5>
    <div class="row"><svg width="12" height="16" viewBox="0 0 12 16"><path d="M6 0a6 6 0 0 0-6 6c0 4.5 6 10 6 10s6-5.5 6-10a6 6 0 0 0-6-6z" fill="#2f8fd6"/><circle cx="6" cy="6" r="2.2" fill="#1a1a1a"/></svg><div>Delacroix &amp; Vella Advocates<br>12/4, Harbour Lane, Valletta<br>88, Olive Grove Street, Mosta</div></div>
    <div class="row"><svg width="14" height="14" viewBox="0 0 14 14"><path d="M3 1 5 4 4 6q1 3 4 4l2-1 3 2-1 2Q5 13 1 3z" fill="#2f8fd6"/></svg><div>555-014-229</div></div>
    <div class="row"><svg width="14" height="14" viewBox="0 0 14 14"><rect x="1" y="3" width="12" height="8" fill="#2f8fd6"/><rect x="3" y="5" width="8" height="2" fill="#1a1a1a"/></svg><div>555-014-229</div></div>
    <div class="row"><svg width="14" height="12" viewBox="0 0 14 12"><rect x="0.5" y="1" width="13" height="10" fill="#2f8fd6"/><path d="m1 2 6 5 6-5" stroke="#1a1a1a" fill="none"/></svg><div>info@dvadvocates.example</div></div>
  </div>
  <div class="map" role="img" aria-label="Street map showing the office location"></div>
  <div class="footer-brand">Delacroix &amp; Vella</div>
  <div class="footer-circles">
    <span style="background:#3b5e9c"></span><span style="background:#2a7fb8"></span><span style="background:#2aa3df"></span><span style="background:#d24a36"></span>
  </div>
  <div class="legal"><span>Terms &amp; Conditions</span>|<span>Privacy Policy</span></div>
</footer>
<div class="copyright">Copyright © 2014 <b>Delacroix &amp; Vella Advocates.</b> All Rights Reserved.</div>

</body>
</html>
```